Silver Lanterns - Media Kit & Rate Card Package for Advertisers

Hi,
I write a lifestyle blog which centres around food, wine and travel. I send my media kit out to potential sponsors, PR companies and product representatives.

I need to make my media kit look gorgeous!
In the kit I would like to have active links to past stories and active social media buttons in the electronic copy.

I don't like how the images are distinct from the text and think perhaps an overlay may look ok with text over a more transparent image.

I like my logo and don't want that to change. I want the kit to look attractive, sophisticated and well branded to silver lanterns.

I would also like to be able to take the media kit to the printers and have a nice glossy kit printed to hand local advertisers.

I have tried to include all the relevant information in the existing kit so a graphic designer can just put the necessary texts, tables and rate cards into and attractive and co-hesive document. I have included a selection of images which suit my website. Feel free to use as many or as few as you think the document requires. If you feel you would like to add a stock image than be my guest. I am interested it seeing a range of designs.

I am only a small blog and am only just breaking even at the moment. I am really hope this media kit makes me look more professional and impressive and enables me to attract a sponsored partnership.

I don't know what the going rate is for this kind of work so if my budget is too lean could you please tell me rather than ignore the job request.

Target Market(s)

Brand Sponsors, Airline Sponsors, PR Agencies, Advertising Purchasers, Tourism Agencies & Departments, Premium Hotel Chains, Package Holiday Specialists, Wellness Retreats, Cruise Lines

Industry/Entity Type

Travel

Font styles to use
Serif

Requirements
Must have
• I need to make my media kit look gorgeous!
• In the electronic copy I would like to have active links to past stories and active social.
• Must include all the tables, text and a rate card.
• Needs Social Media Buttons.
• Needs to use my logo and follow my branding. (I included my logo and a copy of my business card)
Nice to have
• I want it to look, elegant, sophisticated and modern. I want it to have equal focus visually on food, wine and travel.
Should not have
• I don't want it to look boxes or squashed.

```html
<!DOCTYPE html>
<html lang="en">
<head>
<meta charset="UTF-8">
<title>Silver Lanterns – Media Kit – Frequently Asked Questions</title>
<link href="https://fonts.googleapis.com/css2?family=Raleway:wght@200;300&family=Open+Sans:wght@400;600&family=Yanone+Kaffeesatz:wght@300&display=swap" rel="stylesheet">
<style>
  :root {
    --ink: #333333;
    --body-ink: #2e2e2e;
    --accent: #8a6ea6;
    --grey-soft: #8c8c8c;
    --rule: #bdbdbd;
    --paper: #ffffff;
    --band-dark: #c9c9c9;
  }
  * { margin: 0; padding: 0; box-sizing: border-box; }
  html, body {
    width: 900px; height: 1200px; overflow: hidden;
    background: var(--paper);
  }
  .page {
    position: relative; width: 900px; height: 1200px;
    background: var(--paper); color: var(--body-ink);
    font-family: "Open Sans", Arial, sans-serif;
  }
  .brand {
    position: absolute; left: 42px; top: 70px;
    display: flex; align-items: center; gap: 14px;
  }
  .brand-dot {
    width: 22px; height: 22px; border-radius: 50%;
    background: var(--accent);
  }
  .brand-name {
    font-family: "Open Sans", Arial, sans-serif; font-weight: 400;
    font-size: 38px; color: var(--ink); line-height: 1;
  }
  .ornament {
    position: absolute; left: 400px; top: 24px; width: 200px; height: 150px;
    background: radial-gradient(ellipse at 40% 55%, #d9d9d9 0%, #efefef 55%, rgba(255,255,255,0) 75%);
  }
  .social { position: absolute; left: 630px; top: 144px; display: flex; gap: 20px; }
  .social a {
    display: block; width: 46px; height: 46px; border-radius: 50%;
    background: var(--accent);
  }
  .header-rule {
    position: absolute; left: 0; top: 228px; width: 610px; height: 3px;
    background: linear-gradient(to right, var(--rule), rgba(189,189,189,0.2));
  }
  .kit-title {
    position: absolute; right: 32px; top: 206px;
    font-family: "Raleway", Arial, sans-serif; font-weight: 200;
    font-size: 58px; color: var(--grey-soft); line-height: 1;
  }
  .faq-title {
    position: absolute; left: 74px; top: 280px;
    font-family: "Yanone Kaffeesatz", "Arial Narrow", sans-serif; font-weight: 300;
    font-size: 62px; color: var(--accent); line-height: 1;
  }
  .faq { position: absolute; left: 74px; width: 790px; }
  .faq h2 {
    font-weight: 600; font-size: 25px; color: var(--ink);
    margin-bottom: 10px; line-height: 1.25;
    white-space: nowrap;
  }
  .faq p { font-size: 15px; line-height: 1.6; color: var(--body-ink); }
  .faq-why-blogger { top: 400px; }
  .faq-why-me { top: 600px; }
  .faq-charge { top: 836px; }
  .faq-bad-review { top: 972px; }
  .footer-band {
    position: absolute; left: 0; bottom: 0; width: 900px; height: 44px;
    background: linear-gradient(to right, rgba(255,255,255,0) 0%, var(--band-dark) 45%, rgba(255,255,255,0) 100%);
  }
</style>
</head>
<body>
<div class="page">
  <header>
    <div class="brand">
      <span class="brand-dot"></span>
      <span class="brand-name">Silver Lanterns</span>
    </div>
    <div class="ornament" role="img" aria-label="Decorative flourish ornament beside the brand name"></div>
    <nav class="social" aria-label="Social media">
      <a href="#" aria-label="Social profile one"></a>
      <a href="#" aria-label="Social profile two"></a>
      <a href="#" aria-label="Social profile three"></a>
      <a href="#" aria-label="Social profile four"></a>
    </nav>
    <div class="header-rule"></div>
    <div class="kit-title">Media Kit</div>
  </header>

  <h1 class="faq-title">Frequently Asked Questions</h1>

  <section class="faq faq-why-blogger">
    <h2>Why advertise with a blogger online?</h2>
    <p>Media and your audience has moved very quickly away from mainstream media and into online technology and the blogosphere. To reach your audience now you need to connect with them on the platforms they're consuming.</p>
  </section>

  <section class="faq faq-why-me">
    <h2>Why Work With Me?</h2>
    <p>I published my first story on Silver Lanterns in April 2010 and since then the website has grown in popularity, and reader engagement. I have been in the blogging, publishing &amp; marketing industry for over 5 years. I understand the business of blogging, readers expectations and how to deliver a sponsors product in a campaign for maximum reach and engagement.</p>
  </section>

  <section class="faq faq-charge">
    <h2>Why do you charge for your services?</h2>
    <p>Silver Lanterns is a professional publisher in the online marketing industry. My rates represent the exposure I can give your brand and the ongoing costs to stay a leader in the industry.</p>
  </section>

  <section class="faq faq-bad-review">
    <h2>What if you don't like my product, will you write a bad review?</h2>
    <p>I will only work with products and venues I love! I want to create a positive long term relationship with all my sponsors and I only share products, events and experiences I love with my readers. If your product and my website are not a good fit then I will let you know. I will not write the story and I won't charge a fee. I may even be able to suggest a blogger that will be a better fit for your company.</p>
  </section>

  <div class="footer-band"></div>
</div>
</body>
</html>
```